Cutting Edge Property Services Provider is Looking to Update Business Card Design

We are looking to freshen up our business cards to match our cutting edge technology based image.

KORVANEX - Where Care Finds Its Pulse

More information about our company can be found on our website at www.korvanex-demo.net

We integrate technology in a historically low tech industry.

We have appeared on the Brisk 300/3000 list 2 years in a row and we're previously recognized as the 5th Quickest Rising Firm in San Diego.

Our core colors are blue and white, but are not against accents that might improve our image.

We currently have our Mission Statement on our Business Cards in a folding design:
KORVANEX IS THE LEADING BUILDING SERVICES INNOVATOR. BY COMBINING TECHNOLOGY WITH FUNCTIONAL TOOS THAT IMPROVE EFFICIENCY IN THE WORKPLACE, WE PROVIDE UNPARALLELED SERVICE IN THE INDUSTRY. DEVELOPING LASTING RELATIONSHIPS WITH OUR CLIENTS AND ASSOCIATES IS THE CORNERSTONE OF OUR SUCCESS.

We'd like to convey the image of a cutting edge, technology based company. Want the cards to pop.

Target Market(s)

Commercial Property Managers - 20 to 50 year old professionals

Industry/Entity Type

Business

Requirements
Must have
• Must utilize our logo obviously, but are definitely open to using variations on the logo. Utilizing the components of the logo, but maybe in different configurations or backgrounds, etc...

Must use the Name: KORVANEX.
Can also use KORVANEX PROPERTY SERVICES.

Must include the Mission Statement

Must say: Where Care Finds Its Pulse
Nice to have
• We are considering plastic stock, shaped cards, or folding cards.

Nothing over the top or really expensive, but will consider if it conveys innovation and technology.
Should not have
• No images of toilets, buildings, trees, or anything relating to commercial properties.

We want to convey our technology image.

```html
<!DOCTYPE html>
<html lang="en">
<head>
<meta charset="utf-8">
<title>KORVANEX Business Card</title>
<link href="https://fonts.googleapis.com/css2?family=Jost:wght@400;500;700&display=swap" rel="stylesheet">
<style>
  :root {
    --brand-blue: #0b4a7b;
    --tag-blue: #1d5c8a;
    --ink: #333333;
    --card: #ffffff;
    --backdrop: #e8e6e3;
    --label: #222222;
  }
  * { margin: 0; padding: 0; box-sizing: border-box; }
  html, body { width: 1200px; height: 713px; overflow: hidden; }
  body {
    position: relative;
    background: var(--backdrop);
    font-family: "Jost", sans-serif;
    color: var(--ink);
  }
  .side-label {
    position: absolute; top: 28px; width: 526px;
    text-align: center; font-size: 22px; color: var(--label);
  }
  .side-label.front { left: 54px; }
  .side-label.back { left: 640px; }

  .card {
    position: absolute; width: 526px; height: 298px;
    background: var(--card); border-radius: 22px;
    box-shadow: 0 1px 3px rgba(0,0,0,0.15);
    overflow: hidden;
  }
  .card.front-top { left: 54px; top: 72px; }
  .card.front-bottom { left: 54px; top: 372px; }
  .card.back-top { left: 640px; top: 72px; }
  .card.back-bottom { left: 640px; top: 372px; }

  .brand-name {
    color: var(--brand-blue); font-weight: 700; letter-spacing: 2px;
    white-space: nowrap;
  }
  .front-top .brand-name {
    position: absolute; left: 0; right: 0; top: 108px;
    text-align: center; font-size: 64px;
  }
  .back-top .brand-name {
    position: absolute; left: 0; right: 0; top: 92px;
    text-align: center; font-size: 44px;
  }
  .tagline {
    position: absolute; left: 0; right: 0; top: 245px;
    text-align: center; font-size: 18px; color: var(--tag-blue);
  }

  .mission {
    position: absolute; left: 40px; right: 40px; top: 82px;
    text-align: center; font-size: 17.5px; line-height: 23.5px; color: var(--ink);
  }

  .name-band { position: absolute; top: 30px; left: 0; right: 0; height: 40px; }
  .band-left, .band-right { position: absolute; top: 0; height: 40px; background: var(--brand-blue); }
  .band-left { left: 0; width: 58px; }
  .band-right { left: 332px; right: 0; }
  .name-band .brand-name {
    position: absolute; left: 68px; top: 0; line-height: 40px; font-size: 31px;
  }

  .person {
    position: absolute; left: 48px; top: 138px;
    font-size: 20px; color: var(--brand-blue);
  }
  .person .designation { font-size: 15px; }
  .contact-list {
    position: absolute; left: 48px; top: 166px; list-style: none;
  }
  .contact-list li {
    display: flex; align-items: center; height: 22px;
    font-size: 14px; color: var(--ink);
  }
  .contact-list svg { width: 12px; height: 12px; margin-right: 11px; fill: var(--brand-blue); }
</style>
</head>
<body>
  <div class="side-label front">Front</div>
  <div class="side-label back">Back</div>

  <section class="card front-top">
    <div class="brand-name">KORVANEX</div>
  </section>

  <section class="card front-bottom">
    <p class="mission">Korvanex is the leading building services innovator. By combining technology with functional toos that improve efficiency in the workplace, we provide unparalleled service in the industry. Developing lasting relationships with our clients and associates is the cornerstone of our success.</p>
  </section>

  <section class="card back-top">
    <div class="brand-name">KORVANEX</div>
    <p class="tagline">Where Care Finds Its Pulse</p>
  </section>

  <section class="card back-bottom">
    <div class="name-band">
      <div class="band-left"></div>
      <div class="brand-name">KORVANEX</div>
      <div class="band-right"></div>
    </div>
    <p class="person">Your Name, <span class="designation">Designation</span></p>
    <ul class="contact-list">
      <li><svg viewBox="0 0 12 12"><rect x="3" y="0" width="6" height="12" rx="1"/></svg>+12 345 67 8910</li>
      <li><svg viewBox="0 0 12 12"><path d="M2 1h3l1 3-2 1a7 7 0 0 0 3 3l1-2 3 1v3c0 1-1 1-2 1A10 10 0 0 1 1 3c0-1 0-2 1-2z"/></svg>+12 345 67 8910</li>
      <li><svg viewBox="0 0 12 12"><rect x="0" y="2" width="12" height="8" rx="1"/></svg>info@korvanex-demo.net</li>
      <li><svg viewBox="0 0 12 12"><circle cx="6" cy="6" r="5.5"/></svg>www.korvanex-demo.net</li>
      <li><svg viewBox="0 0 12 12"><path d="M6 0l6 6h-2v6H7V8H5v4H2V6H0z"/></svg>123, Abc Street, 0000 City, Country</li>
    </ul>
  </section>
</body>
</html>
```